Letterhead and matching envelope design for a dental office

We need a new stationary design, letterhead and envelope #10, for a dental office in Denver area. We are called Bright Harbor Dental. We want a simple and minimalistic design but not a boring design. I wish to have one good point that makes it look professional. I have attached our logo. Feel free to use either one. I want the design for letterhead and envelope look like a "matching pair" but not look the same. The envelope doesn't have to be white and it will have an address window on bottom left.

Target Market(s)

everyone who visits dentist (adults)

Industry/Entity Type

Dental

Font styles to use
Other font styles liked:
• close to font on logo or something that matches well

Requirements
Must have
• professional
• simple, minimalistic
• unique point that stands out
Nice to have
• matching but not same design for letterhead and envelope
Should not have
• not look like all the other boring designs
• no flowery, distracting feats

```html
<!DOCTYPE html>
<html lang="en">
<head>
<meta charset="utf-8">
<title>Bright Harbor Dental – Letterhead</title>
<link href="https://fonts.googleapis.com/css2?family=Arimo:wght@400;700&family=Open+Sans:wght@400;600;700&display=swap" rel="stylesheet">
<style>
  :root {
    --backdrop: #e9e9ea;
    --paper: #ffffff;
    --green: #3cb44a;
    --green-dark: #2e9a3b;
    --ink: #2b2b2b;
    --body: #555555;
    --muted: #cfcfcf;
  }
  * { box-sizing: border-box; margin: 0; padding: 0; }
  html, body {
    width: 1200px; height: 1066px; overflow: hidden;
    background: var(--backdrop);
  }
  .letterhead {
    position: absolute; left: 250px; top: 38px;
    width: 700px; height: 990px;
    background: var(--paper);
    box-shadow: 0 4px 18px rgba(0,0,0,.12);
    overflow: hidden;
    font-family: "Arimo", Arial, sans-serif;
  }
  .brand {
    position: absolute; left: 56px; top: 56px;
    display: flex; align-items: center; gap: 10px;
  }
  .brand-dot {
    width: 18px; height: 18px; border-radius: 50%;
    background: var(--green);
  }
  .brand-name {
    font-family: "Open Sans", Arial, sans-serif;
    font-weight: 600; font-size: 19px; color: var(--green);
    letter-spacing: .5px;
  }
  .letter {
    position: absolute; left: 56px; top: 300px; width: 560px;
    color: var(--body); font-size: 13px; line-height: 1.4;
  }
  .salutation {
    color: var(--ink); font-weight: 700; font-size: 16px;
    margin-bottom: 16px;
  }
  .letter p { margin-bottom: 16px; }
  .signature {
    position: absolute; left: 56px; top: 640px;
    width: 150px; height: 56px; border-radius: 4px;
    background: linear-gradient(90deg, #f1f1f1, #e4e4e4);
  }
  .footer-rule {
    position: absolute; left: 240px; right: 0; top: 820px;
    height: 1px; background: var(--green);
  }
  .contact {
    position: absolute; right: 40px; top: 842px;
    text-align: right; font-family: "Open Sans", Arial, sans-serif;
    font-size: 12px; color: var(--ink); line-height: 1.5;
  }
  .contact-name { color: var(--green); font-weight: 700; font-size: 13px; }
  .contact-line { display: flex; justify-content: flex-end; align-items: center; gap: 5px; }
  .contact-line svg { width: 12px; height: 12px; }
  .contact-gap { width: 10px; }
  .footer-band {
    position: absolute; left: 0; right: 0; bottom: 0; height: 8px;
    background: var(--green);
  }
  .web-tab {
    position: absolute; right: 0; bottom: 0; width: 260px; height: 34px;
    background: var(--green);
    border-top-left-radius: 18px;
    display: flex; align-items: center; justify-content: center;
    color: #fff; font-family: "Open Sans", Arial, sans-serif;
    font-size: 13px; letter-spacing: .6px;
  }
</style>
</head>
<body>
  <main class="letterhead">
    <header class="brand">
      <span class="brand-dot"></span>
      <span class="brand-name">Bright Harbor Dental</span>
    </header>

    <section class="letter">
      <div class="salutation">Dear Mr. Carter,</div>
      <p>Lorem Ipsum is simply dummy text of the printing and typesetting industry. Lorem Ipsum has been the industry's standard dummy text ever since the 1500s, when an unknown printer took a galley of type and scrambled it to make a type specimen book. It has survived not only five centuries, but also the leap into electronic typesetting, remaining essentially unchanged.</p>
      <p>The standard chunk of Lorem Ipsum used since the 1500s is reproduced below for those interested. Sections 1.10.32 and 1.10.33 from "de Finibus Bonorum et Malorum" by Cicero are also reproduced in their exact original form, accompanied by English versions from the 1914 translation by H. Rackham.</p>
      <p>Lorem Ipsum is simply dummy text of the printing and typesetting industry. Lorem Ipsum has been the industry's standard dummy text ever since the 1500s, when an unknown printer took a galley of type and scrambled it to make a type specimen book. It has survived not only five centuries, but also the leap into electronic typesetting, remaining essentially unchanged. It was popularised in the</p>
    </section>

    <div class="signature" role="img" aria-label="Handwritten signature of the dentist"></div>

    <div class="footer-rule"></div>

    <address class="contact" style="font-style:normal">
      <div class="contact-name">Bright Harbor Dental</div>
      <div>2875 LAKEVIEW DR, SUITE 210 ARVADA, CO 80004</div>
      <div class="contact-line">
        <svg viewBox="0 0 12 12"><circle cx="6" cy="6" r="6" fill="var(--green)"/><path d="M4 3.2l1 1.4-.6.7c.4.9 1.1 1.6 2 2l.7-.6 1.4 1-.5 1c-2.2-.2-4.3-2.3-4.5-4.5z" fill="#fff"/></svg>
        <span>303-555-0147</span>
        <span class="contact-gap"></span>
        <svg viewBox="0 0 12 12"><circle cx="6" cy="6" r="6" fill="var(--green)"/><rect x="3" y="4" width="6" height="4.2" fill="none" stroke="#fff" stroke-width=".8"/><path d="M3 4l3 2.3L9 4" fill="none" stroke="#fff" stroke-width=".8"/></svg>
        <span>hello@brightharbordental.com</span>
      </div>
    </address>

    <div class="footer-band"></div>
    <div class="web-tab">www.brightharbordental.com</div>
  </main>
</body>
</html>
```